Willow Landing - Multifamily Development

Willow Landing is a Luxury Multifamily Development project located in Orange, NJ. This project will be completed in three phases with the first phase about 75% complete. Each phase will have a different name as follows
CEDAR Willow Landing
LANTERN Willow Landing
BRAMBLEWOOD Willow Landing
We are going to install a banner on the side of the first building which will act as advertising for all buildings. We will eventually need advertising that will be in the windows as well as marketing materials . We want the marketing for this project to be similar for all three phases. At the moment, we are starting with this first simple banner. Attached is a rough idea of the look as well as our color palette. If you feel the color palette is a little too monochrome, feel free to propose an accent color. You can also visit our website to see more info on our company as well as the project. www.tarnlv.com Finally, if you need AI files (ie. for the logo), we can send to you. Thanks..

```html
<!DOCTYPE html>
<html lang="en">
<head>
<meta charset="utf-8">
<title>Willow Landing – Banner Set</title>
<link rel="stylesheet" href="https://fonts.googleapis.com/css2?family=Open+Sans:wght@300;400;600;700;800&family=Oswald:wght@600;700&display=swap">
<style>
  :root{
    --navy:#1e2a40;
    --navy-deep:#0b0f17;
    --brand-blue:#4a6aa5;
    --ink:#252525;
    --white:#ffffff;
    --page:#ffffff;
  }
  *{box-sizing:border-box;margin:0;padding:0}
  html,body{width:1200px;height:1126px;overflow:hidden;background:var(--page)}
  body{font-family:"Open Sans",Arial,sans-serif;position:relative;border:1px solid #333}
  .banner{position:absolute;overflow:hidden}
  .photo{position:absolute}
  .abs{position:absolute}
  .brand-name{font-family:"Open Sans",Arial,sans-serif;font-weight:800;color:var(--ink);letter-spacing:.02em;white-space:nowrap;line-height:1.1;text-align:center}
  .phone{font-family:"Oswald","Arial Narrow",sans-serif;font-weight:700;white-space:nowrap;display:flex;align-items:center;line-height:1}
  .phone svg{fill:currentColor;flex:none}
  .web{font-weight:700;color:var(--white);display:flex;align-items:center;white-space:nowrap;line-height:1}
  .rule-soft{height:4px;border-radius:50%;background:radial-gradient(ellipse at center,rgba(255,255,255,.85),rgba(255,255,255,0) 70%)}

  /* Banner A – landscape, light */
  .banner-a{left:66px;top:53px;width:584px;height:484px;border:1px solid #ccc;background:var(--white)}
  .banner-a .photo{inset:0;background:
      linear-gradient(180deg,#ffffff 0%,#eef1f4 22%,#c9d0d8 40%,#a9a58c 52%,#8a7a5a 62%,#6f9a3c 74%,#4f8a2a 100%)}
  .banner-a .brand-name{left:34px;top:60px;width:185px;font-size:28px}
  .banner-a .divider{left:249px;top:20px;height:120px;border-left:1px dotted var(--brand-blue)}
  .banner-a .title{left:260px;top:30px;font-size:31px;font-weight:800;color:var(--brand-blue);letter-spacing:.01em;white-space:nowrap}
  .banner-a .subtitle{left:262px;top:68px;font-size:25px;font-weight:400;color:var(--ink);line-height:1.2;white-space:nowrap}
  .banner-a .footer{left:0;right:0;bottom:0;height:49px;background:var(--navy)}
  .banner-a .web{left:24px;bottom:10px;font-size:25px}
  .banner-a .phone-pill{left:255px;top:413px;width:295px;height:55px;background:var(--brand-blue);border-radius:9px;color:var(--white);justify-content:center;font-size:44px;gap:10px}

  /* Banner B – landscape, dark */
  .banner-b{left:64px;top:572px;width:584px;height:484px;border:1px solid #ccc;background:linear-gradient(180deg,var(--navy-deep) 0%,#18213a 30%,var(--navy) 100%)}
  .banner-b .photo{left:0;right:0;top:95px;bottom:0;background:
      linear-gradient(180deg,#1a1d22 0%,#2c2c30 25%,#b4a48c 45%,#a08c72 62%,#8c7a62 75%,#6a7e4a 88%,#5a6a44 100%)}
  .banner-b .photo-fade{left:0;top:260px;width:360px;bottom:0;background:linear-gradient(180deg,rgba(255,255,255,0),rgba(255,255,255,.95) 60%,#fff)}
  .banner-b .title{left:0;right:0;top:12px;text-align:center;font-size:35px;font-weight:300;color:var(--white);letter-spacing:.02em;white-space:nowrap}
  .banner-b .rule-soft{left:210px;width:170px;top:57px}
  .banner-b .subtitle{left:0;right:0;top:68px;text-align:center;font-size:19px;letter-spacing:.2em;color:var(--white);font-weight:400;white-space:nowrap}
  .banner-b .brand-name{left:30px;top:388px;width:230px;font-size:29px}
  .banner-b .phone-pill{left:288px;top:398px;width:226px;height:42px;background:var(--brand-blue);border-radius:7px 7px 0 0;color:var(--white);justify-content:center;font-size:32px;gap:8px}
  .banner-b .footer{left:288px;right:0;top:437px;bottom:0;background:var(--navy)}
  .banner-b .web{left:300px;top:450px;font-size:25px}

  /* Banner C – vertical, dark top */
  .banner-c{left:695px;top:53px;width:197px;height:756px;background:linear-gradient(180deg,var(--navy-deep) 0%,#161d2c 20%,var(--navy) 30%)}
  .banner-c .title{left:0;right:0;top:18px;text-align:center;font-size:29px;font-weight:300;color:var(--white);line-height:1.02}
  .banner-c .rule-soft{left:45px;width:108px;top:85px}
  .banner-c .subtitle{left:0;right:0;top:96px;text-align:center;font-size:24px;color:var(--white);line-height:1.08}
  .banner-c .photo{left:0;right:0;top:195px;height:380px;background:
      linear-gradient(180deg,#2a2c30 0%,#b0a08a 30%,#9c8a72 48%,#5f7a3a 68%,#8a9296 82%,#ffffff 100%)}
  .banner-c .lower{left:0;right:0;top:575px;bottom:0;background:var(--white)}
  .banner-c .brand-name{left:0;right:0;top:588px;font-size:19px}
  .banner-c .dotted{left:11px;right:11px;top:648px;border-top:1px dotted var(--brand-blue)}
  .banner-c .phone{left:0;right:0;top:661px;justify-content:center;font-size:29px;color:var(--ink);gap:6px}
  .banner-c .arc{left:0;bottom:0}
  .banner-c .web{left:0;right:0;top:728px;justify-content:center;font-size:25px}
  .banner-c .globe{left:86px;top:697px;color:var(--brand-blue)}

  /* Banner D – vertical, light top */
  .banner-d{left:937px;top:55px;width:197px;height:756px;border:1px solid #ddd;background:var(--white)}
  .banner-d .brand-name{left:0;right:0;top:52px;font-size:20px}
  .banner-d .title{left:0;right:0;top:128px;text-align:center;font-size:32px;font-weight:400;color:var(--brand-blue);line-height:1.0}
  .banner-d .shadow-rule{left:48px;width:102px;top:200px;height:5px;border-radius:50%;background:radial-gradient(ellipse at center,rgba(40,50,70,.55),rgba(40,50,70,0) 70%)}
  .banner-d .photo{left:0;right:0;top:210px;height:340px;background:
      linear-gradient(180deg,#ffffff 0%,#dfe4ea 12%,#a89a7c 32%,#c9c2b4 50%,#5e9632 70%,#4f8a2a 88%,#27331f 100%)}
  .banner-d .lower{left:0;right:0;top:550px;bottom:0;background:var(--navy)}
  .banner-d .phone{left:0;right:0;top:520px;justify-content:center;font-size:27px;color:var(--white);gap:6px}
  .banner-d .tag-box{left:22px;top:559px;width:154px;height:113px;background:var(--brand-blue);padding:28px 0 0 7px;color:var(--white);font-size:24px;line-height:1.05}
  .banner-d .arc{left:0;bottom:0}
  .banner-d .globe{left:84px;top:683px;color:var(--white)}
  .banner-d .web{left:0;right:0;top:728px;justify-content:center;font-size:25px}
</style>
</head>
<body>

<svg width="0" height="0" style="position:absolute" aria-hidden="true">
  <symbol id="ico-phone" viewBox="0 0 24 24">
    <path d="M6.6 10.8a15 15 0 006.6 6.6l2.2-2.2a1 1 0 011-.25 11.4 11.4 0 003.6.6 1 1 0 011 1V20a1 1 0 01-1 1A17 17 0 013 4a1 1 0 011-1h3.5a1 1 0 011 1c0 1.25.2 2.45.57 3.57a1 1 0 01-.25 1z"/>
  </symbol>
  <symbol id="ico-globe" viewBox="0 0 24 24">
    <g fill="none" stroke="currentColor" stroke-width="1.6">
      <circle cx="12" cy="12" r="10"/>
      <ellipse cx="12" cy="12" rx="4.5" ry="10"/>
      <line x1="2" y1="12" x2="22" y2="12"/>
      <path d="M4 6.5h16M4 17.5h16"/>
    </g>
  </symbol>
</svg>

<!-- Banner A -->
<section class="banner banner-a">
  <div class="photo" role="img" aria-label="Photo of a white two-storey house with timber posts, green lawn and autumn trees under a cloudy sky"></div>
  <div class="abs brand-name">TARN<br>PROPERTIES</div>
  <div class="abs divider"></div>
  <div class="abs title">WILLOW LANDING</div>
  <div class="abs subtitle">Luxury Apartment<br>Rentals</div>
  <div class="abs footer"></div>
  <div class="abs web"><svg width="28" height="28" style="color:#fff;margin-right:12px"><use href="#ico-globe"/></svg>TARNLV.COM</div>
  <div class="abs phone phone-pill"><svg width="32" height="32"><use href="#ico-phone"/></svg>555 240 1187</div>
</section>

<!-- Banner B -->
<section class="banner banner-b">
  <div class="photo" role="img" aria-label="Photo of a beige craftsman house with dark roof, lit entry and garage at dusk"></div>
  <div class="abs photo-fade"></div>
  <div class="abs title">WILLOW LANDING</div>
  <div class="abs rule-soft"></div>
  <div class="abs subtitle">LUXURY APARTMENT RENTALS</div>
  <div class="abs brand-name">TARN<br>PROPERTIES</div>
  <div class="abs phone phone-pill"><svg width="26" height="26"><use href="#ico-phone"/></svg>555 240 1187</div>
  <div class="abs footer"></div>
  <div class="abs web"><svg width="28" height="28" style="color:#fff;margin-right:12px"><use href="#ico-globe"/></svg>TARNLV.COM</div>
</section>

<!-- Banner C -->
<section class="banner banner-c">
  <div class="abs title">WILLOW<br>LANDING</div>
  <div class="abs rule-soft"></div>
  <div class="abs subtitle">luxury<br>apartment<br>rentals</div>
  <div class="photo" role="img" aria-label="Photo of a beige craftsman house gable with lit front door and wet driveway"></div>
  <div class="abs lower"></div>
  <div class="abs brand-name">TARN<br>PROPERTIES</div>
  <div class="abs dotted"></div>
  <div class="abs phone"><svg width="20" height="20" style="color:var(--brand-blue)"><use href="#ico-phone"/></svg>555 240 1187</div>
  <svg class="abs arc" width="197" height="62" viewBox="0 0 197 62" aria-hidden="true">
    <path d="M0 20 Q98 -6 197 20 V62 H0 Z" fill="var(--navy)"/>
  </svg>
  <svg class="abs globe" width="24" height="24"><use href="#ico-globe"/></svg>
  <div class="abs web">TARNLV.COM</div>
</section>

<!-- Banner D -->
<section class="banner banner-d">
  <div class="abs brand-name">TARN<br>PROPERTIES</div>
  <div class="abs title">WILLOW<br>LANDING</div>
  <div class="photo" role="img" aria-label="Photo of a white house with timber posts and a wide green lawn"></div>
  <div class="abs shadow-rule"></div>
  <div class="abs lower"></div>
  <div class="abs phone"><svg width="18" height="18"><use href="#ico-phone"/></svg>555 240 1187</div>
  <div class="abs tag-box">luxury<br>apartment<br>rentals</div>
  <svg class="abs arc" width="197" height="70" viewBox="0 0 197 70" aria-hidden="true">
    <path d="M0 26 Q98 -10 197 26 V70 H0 Z" fill="var(--navy-deep)" opacity=".55"/>
  </svg>
  <svg class="abs globe" width="30" height="30"><use href="#ico-globe"/></svg>
  <div class="abs web">TARNLV.COM</div>
</section>

</body>
</html>
```